Detail Shop Business card design

i need a business card design for my new detailing company called 'Brisk's Polish Works'. i want an all black and white design . simple, direct and to the point. i want the designer to choose a fitting font to match the logothe front should have logo, address, phone and email and the back side should have a slogan and text indicating that we offer services on anything including cars, trucks, motorcycles and RVs. slogan will read "we take pride in your ride"
maybe also very small on the back side the IG icon with Brisks_Polish_Works

phone 208.417.6352
address 3847 E Larkin Ave
Spokane WA 99214
email: BrisksPolish@mailvexo.com

Target Market(s)

all ages , auto enthusiasts

Industry/Entity Type

Automotive

Contact Information for Business Card

the front should have logo, address, phone and email and the back side should have a slogan and text indicating that we offer services on anything including cars, trucks, motorcycles and RVs. slogan will read "we take pride in your ride"

phone 208.417.6352
address 3847 E Larkin Ave
Spokane WA 99214

Colors
000000
ffffff

Requirements
Must have
• bold font and very simple design with good spacing
Nice to have
• anything creative from the designer indicating we service any types of vehicles
Should not have
• any colors ,

```html
<!DOCTYPE html>
<html lang="en">
<head>
<meta charset="utf-8">
<title>Brisk's Polish Works – Card Back</title>
<link href="https://fonts.googleapis.com/css2?family=Bitter:wght@800&family=Lobster&display=swap" rel="stylesheet">
<style>
  :root {
    --ink: #1a1a1a;
    --paper: #ffffff;
    --mark-light: #ececec;
    --mark-mid: #e0e0e0;
  }
  html, body {
    margin: 0;
    padding: 0;
    width: 1200px;
    height: 1200px;
    overflow: hidden;
    background: var(--paper);
  }
  .canvas {
    position: relative;
    width: 1200px;
    height: 1200px;
    background: var(--paper);
  }
  .brand-backdrop {
    position: absolute;
    left: 0;
    top: 256px;
    width: 1200px;
    height: 686px;
    background: radial-gradient(ellipse at 45% 55%, var(--mark-mid) 0%, var(--mark-light) 55%, var(--paper) 100%);
  }
  .services {
    position: absolute;
    left: 240px;
    top: 314px;
    font-family: 'Bitter', Georgia, serif;
    font-weight: 800;
    color: var(--ink);
  }
  .services-heading {
    margin: 0;
    font-size: 42px;
    line-height: 1;
    letter-spacing: -0.5px;
  }
  .services-list {
    list-style: none;
    margin: 22px 0 0 56px;
    padding: 0;
  }
  .services-list li {
    font-size: 42px;
    line-height: 66px;
  }
  .services-list li::before {
    content: "\2605";
    display: inline-block;
    width: 48px;
    font-size: 34px;
  }
  .slogan {
    position: absolute;
    left: 0;
    width: 1200px;
    top: 680px;
    margin: 0;
    text-align: center;
    font-family: 'Lobster', cursive;
    font-size: 62px;
    color: var(--ink);
  }
  .social {
    position: absolute;
    left: 308px;
    top: 810px;
    display: flex;
    align-items: center;
    gap: 34px;
    font-family: 'Bitter', Georgia, serif;
    font-weight: 800;
    font-size: 44px;
    color: var(--ink);
  }
  .social-dot {
    width: 52px;
    height: 52px;
    border: 6px solid var(--ink);
    border-radius: 50%;
    box-sizing: border-box;
  }
</style>
</head>
<body>
  <main class="canvas">
    <div class="brand-backdrop" role="img" aria-label="Faint brand emblem with a hot rod, placed behind the text"></div>

    <section class="services">
      <h2 class="services-heading">We service anything including:</h2>
      <ul class="services-list">
        <li>Cars</li>
        <li>Trucks</li>
        <li>Motorcycles</li>
        <li>RVs</li>
      </ul>
    </section>

    <p class="slogan">"We Take Pride in Your Ride"</p>

    <div class="social">
      <span class="social-dot" aria-hidden="true"></span>
      <span class="social-handle">Brisks_Polish_Works</span>
    </div>
  </main>
</body>
</html>
```